Real Estate investment company needs billboard designs

This is our website: https://brightlanepropertygroup.com/
We are looking for some billboard concepts that uses our CEO in the design. I have attached some images and 1 billboard design that someone in our industry uses, but we don't want it exactly like his.

Industry/Entity Type

real estate

Colors

Designer to choose colors to be used in the design.

Requirements
Must have
• Company colors from websiute

```html
<!DOCTYPE html>
<html lang="en">
<head>
<meta charset="UTF-8">
<title>Bright Lane Property Group – Billboard</title>
<link href="https://fonts.googleapis.com/css2?family=Oswald:wght@700&family=Poppins:wght@700;800&display=swap" rel="stylesheet">
<style>
  :root {
    --navy: #1d1b3b;
    --red: #ec2227;
    --white: #ffffff;
    --page: #ffffff;
    --room-light: #f4efe8;
    --room-mid: #e2d8cc;
    --shirt-light: #b9cde3;
    --shirt-mid: #8fadd0;
  }
  * { margin: 0; padding: 0; box-sizing: border-box; }
  html, body {
    width: 1110px;
    height: 1200px;
    overflow: hidden;
    background: var(--page);
  }
  .billboard {
    position: absolute;
    left: 55px;
    top: 370px;
    width: 1000px;
    height: 461px;
    background: var(--navy);
    overflow: hidden;
    box-shadow: 0 6px 22px rgba(0, 0, 0, 0.18);
  }
  .billboard__shapes {
    position: absolute;
    inset: 0;
  }
  .headline {
    position: absolute;
    left: 54px;
    top: 36px;
    font-family: "Oswald", "Arial Narrow", sans-serif;
    font-weight: 700;
    font-size: 86px;
    line-height: 84px;
    color: var(--white);
    text-transform: uppercase;
    letter-spacing: 0.5px;
    white-space: nowrap;
  }
  .headline__line { display: block; }
  .headline__accent { color: var(--red); }
  .contact {
    position: absolute;
    left: 56px;
    top: 352px;
    color: var(--white);
    font-family: "Poppins", Arial, sans-serif;
    white-space: nowrap;
  }
  .contact__phone {
    display: block;
    font-weight: 800;
    font-size: 51px;
    line-height: 56px;
    letter-spacing: 0.5px;
  }
  .contact__web {
    display: block;
    font-weight: 700;
    font-size: 22px;
    line-height: 28px;
  }
  .brand {
    position: absolute;
    left: 750px;
    top: 338px;
    width: 250px;
    height: 123px;
    display: flex;
    flex-direction: column;
    justify-content: center;
    padding-left: 22px;
    background: var(--navy);
    font-family: "Poppins", Arial, sans-serif;
    font-weight: 700;
    color: var(--white);
    text-transform: uppercase;
    white-space: nowrap;
  }
  .brand__name { font-size: 27px; line-height: 32px; letter-spacing: 0.5px; }
  .brand__tag { font-size: 14px; line-height: 20px; letter-spacing: 2px; }
</style>
</head>
<body>
  <section class="billboard">
    <svg class="billboard__shapes" width="1000" height="461" viewBox="0 0 1000 461">
      <defs>
        <linearGradient id="roomTone" x1="0" y1="0" x2="1" y2="1">
          <stop offset="0" stop-color="#f4efe8"/>
          <stop offset="1" stop-color="#e2d8cc"/>
        </linearGradient>
        <linearGradient id="shirtTone" x1="0" y1="0" x2="0" y2="1">
          <stop offset="0" stop-color="#b9cde3"/>
          <stop offset="1" stop-color="#8fadd0"/>
        </linearGradient>
      </defs>
      <rect class="contact-band" x="0" y="190" width="500" height="271" fill="var(--red)"/>
      <path class="headline-panel" d="M0 0 H700 V338 H150 A150 150 0 0 1 0 188 Z" fill="var(--navy)"/>
      <polygon class="family-photo" role="img" aria-label="Photo of a family relaxing on a sofa with their dog in a bright living room"
               points="647,0 1000,0 1000,338 600,338" fill="url(#roomTone)"/>
      <path class="ceo-photo" role="img" aria-label="Photo of the company CEO in a light denim shirt pointing up at the headline"
            d="M472 461 V160 Q472 30 612 30 Q752 30 752 160 V461 Z" fill="url(#shirtTone)"/>
    </svg>

    <h1 class="headline">
      <span class="headline__line">Sell Your</span>
      <span class="headline__line">House</span>
      <span class="headline__line headline__accent">Fast!</span>
    </h1>

    <p class="contact">
      <span class="contact__phone">865-555-0142</span>
      <span class="contact__web">brightlanepropertygroup.com</span>
    </p>

    <div class="brand">
      <span class="brand__name">Bright Lane</span>
      <span class="brand__tag">Property Group</span>
    </div>
  </section>
</body>
</html>
```